Flyer Promoting Dental Benefit Program

I want to promote a dental benefit program to my patients that do not have dental insurance. This flyer would be posted in our waiting room and where people make payments. The goal would be to get those interested to request more information and enroll in the program. I have a card that will be issued that has a logo. Theflyer and card should feel congruent. I've uploaded a file with a copy of that card.
The plan costs $290/person. It includes 2 cleanings, exams, and x-rays. It also includes a 20% discount off of our standard fees. The plan or membership lasts for one year. It is only available to those without insurance. It is also important to let people know that this is not insurance (some kind of a disclaimer).
Updates
This plan is only available to patients at my office. The contact information is: Harborview Dental, 2718 West 4600 North Suite 209, Salt Lake City, Utah 84157. (801) 563-9071. info@harborviewdental-example.com. It is not necessary to include contact information as this flyer will be used as in-office promotion.
Target Market(s)
Those without dental insurance, but have resources to afford dental care.
Industry/Entity Type
Insurance
Look and feel
Each slider illustrates characteristics of the customer's brand and the style your logo design should communicate.

```html
<!DOCTYPE html>
<html lang="en">
<head>
<meta charset="utf-8">
<title>Harborview Care Plan Flyer</title>
<link href="https://fonts.googleapis.com/css2?family=Open+Sans:wght@400;600;700&family=Roboto+Condensed:wght@700&display=swap" rel="stylesheet">
<style>
  :root {
    --green: #3f9b3f;
    --green-light: #8cc97a;
    --ink: #333333;
    --ink-soft: #555555;
    --paper: #ffffff;
    --backdrop: #e9e9e9;
    --grass: #7f9a45;
    --hair-light: #d9b27a;
    --skin: #f0c9ad;
    --hair-dark: #6b4a2e;
  }
  * { margin: 0; padding: 0; box-sizing: border-box; }
  html, body {
    width: 931px;
    height: 1200px;
    overflow: hidden;
    background: var(--backdrop);
  }
  .flyer {
    position: absolute;
    left: 74px;
    top: 50px;
    width: 782px;
    height: 1100px;
    background: var(--paper);
    box-shadow: 0 2px 10px rgba(0,0,0,0.15);
    font-family: "Open Sans", Arial, sans-serif;
    color: var(--ink);
  }
  .hero {
    position: absolute;
    left: 170px;
    top: 25px;
    width: 422px;
    height: 422px;
    border-radius: 50%;
    background: var(--green);
    padding: 10px;
  }
  .hero-inner {
    width: 100%;
    height: 100%;
    border-radius: 50%;
    background: var(--green-light);
    padding: 12px;
  }
  .hero-photo {
    width: 100%;
    height: 100%;
    border-radius: 50%;
    background:
      radial-gradient(ellipse 55% 40% at 55% 42%, var(--skin) 0%, rgba(240,201,173,0) 100%),
      linear-gradient(160deg, var(--grass) 0%, var(--hair-light) 30%, var(--skin) 52%, #c98f6a 68%, var(--hair-dark) 88%);
  }
  .hero-shadow {
    position: absolute;
    left: 276px;
    top: 450px;
    width: 210px;
    height: 12px;
    border-radius: 50%;
    background: radial-gradient(ellipse at center, rgba(0,0,0,0.4) 0%, rgba(0,0,0,0) 70%);
  }
  .brand {
    position: absolute;
    top: 484px;
    left: 208px;
    display: flex;
    align-items: center;
    gap: 16px;
  }
  .brand-dot {
    width: 114px;
    height: 114px;
    border-radius: 50%;
    background: var(--green);
    flex: none;
  }
  .brand-name {
    font-weight: 700;
    font-size: 40px;
    line-height: 46px;
    color: var(--ink);
  }
  .headline {
    position: absolute;
    top: 660px;
    left: 0;
    width: 100%;
    text-align: center;
    font-family: "Roboto Condensed", "Arial Narrow", sans-serif;
    font-weight: 700;
    font-size: 43px;
    line-height: 52px;
    color: var(--green);
  }
  .includes {
    position: absolute;
    top: 878px;
    left: 0;
    width: 100%;
    text-align: center;
    font-weight: 600;
    font-size: 23px;
    letter-spacing: 0.5px;
    color: var(--ink-soft);
  }
  .discount {
    position: absolute;
    top: 916px;
    left: 0;
    width: 100%;
    text-align: center;
    font-weight: 700;
    font-size: 30px;
    letter-spacing: -0.5px;
    color: var(--ink);
  }
  .disclaimer {
    position: absolute;
    top: 986px;
    left: 0;
    width: 100%;
    text-align: center;
    font-size: 12.5px;
    line-height: 21px;
    color: var(--ink);
  }
  .call-bar {
    position: absolute;
    left: 0;
    bottom: 0;
    width: 100%;
    height: 56px;
    background: var(--green);
    color: var(--paper);
    display: flex;
    justify-content: center;
    align-items: center;
    gap: 10px;
  }
  .call-label { font-size: 23px; font-weight: 400; }
  .call-number {
    font-family: "Roboto Condensed", "Arial Narrow", sans-serif;
    font-weight: 700;
    font-size: 30px;
    letter-spacing: 1px;
  }
</style>
</head>
<body>
  <main class="flyer">
    <div class="hero">
      <div class="hero-inner">
        <div class="hero-photo" role="img" aria-label="Photo of a smiling young couple lying head to head on green grass"></div>
      </div>
    </div>
    <div class="hero-shadow"></div>

    <div class="brand">
      <span class="brand-dot"></span>
      <span class="brand-name">Harborview<br>Care Plan</span>
    </div>

    <h1 class="headline">Dental benefit program to<br>my patients that do not have<br>dental insurance</h1>

    <p class="includes">IT INCLUDES 2 CLEANINGS, EXAMS, &amp; X-RAYS</p>
    <p class="discount">20% discount off our standard fees</p>

    <p class="disclaimer">
      The plan or membership lasts for one year. It is only available to those without insurance.<br>
      Please note: this plan is not dental insurance and is offered only to patients of our office.
    </p>

    <footer class="call-bar">
      <span class="call-label">Call</span>
      <span class="call-number">(801) 563-9071</span>
    </footer>
  </main>
</body>
</html>
```